Falkrin homes and renovations business card design.

Would like some new card designs utilizing my new logo that look professional. I am open to different colors on the logo or utilize the same ones we have. I like the original concept but would like to see some fresh ideas and build on what we have already done.

Target Market(s)

Custom home building industry, Real estate sales, Renovation projects.

Industry/Entity Type

Home Builder

Contact Information for Business Card

Falkrin Homes and Renovations
2871 96th Avenue
Corwin Ridge, Northland
T2R3W8
Home : 403- 718-4063 Cell: 403- 294-5170

My info is : Dax Falkrin, President and CEO
email: falkrinhomes@maildrop-example.net
Website: falkrinhomes-example.com
websit

Requirements
Must have
• Must Use my new logo design. I am open to different colors on the logo or utilize the same ones in the existing design. I can upload the original logo design if needed.

```html
<!DOCTYPE html>
<html lang="en">
<head>
<meta charset="utf-8">
<title>Falkrin Homes and Renovations – Business Card</title>
<link rel="stylesheet" href="https://fonts.googleapis.com/css2?family=Open+Sans:wght@400;600;700&display=swap">
<style>
  :root {
    --backdrop: #9a9a9a;
    --card: #0c0c0c;
    --card-edge: #1a1a1a;
    --gold: #c8932a;
    --yellow: #f2b705;
    --white: #f4f4f4;
    --rule: #4a3a12;
  }
  * { margin: 0; padding: 0; box-sizing: border-box; }
  html, body {
    width: 1200px; height: 900px; overflow: hidden;
    background: var(--backdrop);
    font-family: "Open Sans", sans-serif;
  }
  .sheet { position: relative; width: 1200px; height: 900px; }
  .card {
    position: absolute; left: 285px; width: 630px; height: 360px;
    background: radial-gradient(ellipse at 50% 40%, var(--card-edge), var(--card) 70%);
    box-shadow: 0 6px 18px rgba(0,0,0,.35);
  }
  .card--front { top: 60px; }
  .card--back { top: 480px; }

  .brand {
    position: absolute; display: flex; align-items: center; gap: 14px;
    color: var(--gold); font-weight: 600; text-transform: uppercase;
  }
  .brand__square { width: 14px; height: 14px; background: var(--gold); flex: none; }
  .brand__name { line-height: 1.05; }
  .brand__name span { display: block; }
  .brand__main { letter-spacing: 1px; }
  .brand__sub { letter-spacing: .5px; }

  .card--front .brand { left: 50%; top: 50%; transform: translate(-50%, -50%); }
  .card--front .brand__main { font-size: 52px; }
  .card--front .brand__sub { font-size: 18px; }

  .card--back .brand { right: 60px; top: 70px; }
  .card--back .brand__main { font-size: 42px; }
  .card--back .brand__sub { font-size: 14px; }

  .person { position: absolute; left: 50px; top: 110px; }
  .person__name { color: var(--yellow); font-weight: 700; font-size: 22px; letter-spacing: .5px; text-transform: uppercase; }
  .person__role { color: var(--white); font-size: 14px; }

  .contacts { list-style: none; margin-top: 10px; }
  .contacts li {
    display: flex; align-items: center; gap: 10px;
    color: var(--white); font-size: 15px; line-height: 23px;
  }
  .contacts svg { width: 13px; height: 13px; fill: var(--yellow); flex: none; }

  .divider { position: absolute; left: 230px; right: 40px; top: 160px; height: 1px; background: var(--rule); }

  .office { position: absolute; right: 50px; top: 262px; text-align: right; font-style: normal; }
  .office__name { color: var(--yellow); font-weight: 600; font-size: 16px; }
  .office__line { color: var(--white); font-size: 15px; line-height: 21px; }
</style>
</head>
<body>
<main class="sheet">

  <section class="card card--front" aria-label="Card front">
    <div class="brand">
      <span class="brand__square"></span>
      <p class="brand__name"><span class="brand__main">Falkrin</span><span class="brand__sub">Homes and Renovations</span></p>
    </div>
  </section>

  <section class="card card--back" aria-label="Card back">
    <div class="brand">
      <span class="brand__square"></span>
      <p class="brand__name"><span class="brand__main">Falkrin</span><span class="brand__sub">Homes and Renovations</span></p>
    </div>

    <div class="divider"></div>

    <div class="person">
      <h1 class="person__name">Dax Falkrin</h1>
      <p class="person__role">President and CEO</p>
      <ul class="contacts">
        <li><svg viewBox="0 0 16 16" aria-hidden="true"><path d="M3 1h3l1.5 4-2 1.3a9 9 0 0 0 4.2 4.2L11 8.5l4 1.5v3a2 2 0 0 1-2 2A12 12 0 0 1 1 3a2 2 0 0 1 2-2z"/></svg>403- 718-4063</li>
        <li><svg viewBox="0 0 16 16" aria-hidden="true"><path d="M4 0h8a1 1 0 0 1 1 1v14a1 1 0 0 1-1 1H4a1 1 0 0 1-1-1V1a1 1 0 0 1 1-1zm1 2v10h6V2zm3 11a1 1 0 1 0 0 2 1 1 0 0 0 0-2z"/></svg>403- 294-5170</li>
        <li><svg viewBox="0 0 16 16" aria-hidden="true"><path d="M0 3h16v10H0zm1.5 1.2v.4L8 9l6.5-4.4v-.4z"/></svg>falkrinhomes@maildrop-example.net</li>
        <li><svg viewBox="0 0 16 16" aria-hidden="true"><circle cx="8" cy="8" r="7"/></svg>www.falkrinhomes-example.com</li>
      </ul>
    </div>

    <address class="office">
      <p class="office__name">Falkrin homes and Renovations</p>
      <p class="office__line">2871 96th Avenue</p>
      <p class="office__line">Corwin Ridge, Northland ,T2R3W8</p>
    </address>
  </section>

</main>
</body>
</html>
```